Cruise Booking Website

Cruise search and booking website

This project is a redesign of a cruise booking website we did a few years ago.

The current website is located here: http://voyage.pylonworks.example/en/

It's not fully functional but gives you ad idea how miserable the old design was.

All the information about cruises, cruise lines, destinations, ports and shore excursions will be similar to http://www.sailquest.example/
Actual search pages (form, results, single result, sailing and cabin selection, ship info, booking) will have EXACTLY the same info as sailquest.example

We like the style of http://harborfleetdesk.example, it's quite modern, good spacing, not overloaded with information. So you can use it as an example of what we like, not what we want as a final result for us. Please, don't copy it. The result should not be possible to resemble the harborfleetdesk.example, because our site has to be unique. This is important!
If you submit a design that clearly reminds another cruise site it will be rejected!

Also the mockup provided is just to give you the basic structure and show what information has to be present on the page. It doesn't mean the layout has to be the same as a mockup. The layout is up to the designer.

I've updated the mockup to be more generic so it doesn't confuse you:
https://files.boxvault.example/s/k7m2qp9wz4hx/Home%20page.png

When you're adding social sharing icons like plazanet/chirpline you have to use chinese ones instead:
https://files.boxvault.example/s/t3nr8vx5lc2e/chinese-social-icons.png
Originals: http://minilk.example/qR7t

We'll start with home page first and after it's approved inner pages can be designed.

I know the cost of the project doesn't look high, but the task is straight forward and doesn't require to be very original, it's better to follow existing design and layout patterns that proved to work well.
That's why I encourage you to choose a template to build the design on top of one of https://themeparlor.example/ themes if it will save the design work, will be easier and faster for you. So it will be more like a customization than a new design from scratch.

Mockups, site map and logo files:
- https://files.boxvault.example/sh/h48dm2rs73fkpw/QvnbW2Xz8e

Website tree:
- https://sheets.papernest.example/document/d/7xPqR2mLw9sTk4VbN8cHj3YzA6eUf5GdKo1iMnBv/edit?usp=sharing
Updates

So far a lot of designs are just copying http://www.harborfleetdesk.example/ - we don't like it!

We like the style of harborfleetdesk.example, it's quite modern, good spacing, not overloaded with information. So you can use it as an example of what we like, not what we want as a final result for us. Please, don't copy it. The result should not be possible to resemble the harborfleetdesk.example, because our site has to be unique. This is important!

Target Market(s)

Chinese travellers

Industry/Entity Type

Build

Requirements
Must have
• * White, blue and red
* Large spacing, not too much information cramped into a small space like sailquest.example or the current website
* More "hidden" info in popups, tabs and so on, so not to many things are visible at the same time
* Compatible with kestrel scaffold styling (for easier coding):
- http://kestrelkit.codeshelf.example/scaffold/index.html
- http://skinmarket.example/
* Feel free to propose to build the design on top of one of https://themeparlor.example/ themes if it will save the design work, will be easier and faster for you

```html
<!DOCTYPE html>
<html lang="en">
<head>
<meta charset="utf-8">
<title>Cruise Results – Haiyue Cruise</title>
<link href="https://fonts.googleapis.com/css2?family=Open+Sans:wght@400;600;700&family=Noto+Sans+SC:wght@400;700&display=swap" rel="stylesheet">
<style>
:root{
  --blue:#2b7bc4;
  --blue-dark:#1e5f9c;
  --red:#d0312d;
  --ink:#333;
  --muted:#777;
  --line:#e2e2e2;
  --band:#f1f1f1;
  --nav:#3a3a3a;
  --footer:#2d2d2d;
  --footer-deep:#1f1f1f;
  --white:#fff;
}
*{box-sizing:border-box;margin:0;padding:0}
html,body{width:793px;height:1200px;overflow:hidden}
body{font-family:"Open Sans","Noto Sans SC",sans-serif;color:var(--ink);background:var(--white);position:relative;font-size:10px}
.wrap{position:absolute;left:93px;width:610px}

/* header */
.site-header{position:absolute;top:0;left:0;width:793px;height:77px}
.brand{position:absolute;left:93px;top:18px;display:flex;align-items:center;gap:8px}
.brand-mark{width:34px;height:34px;border-radius:50%;background:var(--blue)}
.brand-name{font-size:24px;font-weight:700;color:var(--blue);line-height:1}
.brand-url{position:absolute;left:135px;top:54px;font-size:9px;color:var(--muted)}
.header-tools{position:absolute;right:90px;top:8px;text-align:right}
.socials{display:flex;gap:5px;justify-content:flex-end;align-items:center}
.socials span{width:14px;height:14px;border-radius:3px;background:#9aa6b2}
.socials .lang{width:auto;height:auto;background:none;font-size:9px;color:var(--muted);margin-left:4px}
.call{display:flex;align-items:center;gap:6px;margin-top:10px;justify-content:flex-end}
.call-label{font-size:10px;color:var(--muted);line-height:1.2}
.call-number{font-size:15px;font-weight:700;color:var(--blue);line-height:1}
.account{margin-top:6px;display:flex;gap:4px;justify-content:flex-end}
.account a{font-size:8px;color:var(--white);background:var(--blue);padding:2px 6px;border-radius:2px;text-decoration:none}

/* nav */
.main-nav{position:absolute;top:77px;left:0;width:793px;height:24px;background:var(--nav)}
.main-nav ul{list-style:none;display:flex;position:absolute;left:93px;height:24px}
.main-nav li{font-size:9.5px;color:#eee;padding:0 9px;line-height:24px;border-right:1px solid #4a4a4a}
.main-nav li.active{background:var(--blue)}
.breadcrumb{position:absolute;top:101px;left:0;width:793px;height:24px;background:var(--band);border-bottom:1px solid var(--line)}
.breadcrumb p{position:absolute;left:93px;line-height:24px;font-size:8.5px;color:var(--muted)}

/* results */
.results{position:absolute;left:93px;top:148px;width:408px}
.results-head{display:flex;align-items:baseline;gap:8px;border-bottom:1px solid var(--line);padding-bottom:6px}
.results-head h1{font-size:18px;color:var(--blue);font-weight:600}
.results-head small{font-size:8.5px;color:var(--muted)}
.result{position:relative;margin-top:12px;height:140px;border:1px solid var(--line);padding:8px;display:flex;gap:12px}
.result-photo{width:112px;height:80px;background:linear-gradient(180deg,#7fb4e2 0%,#cfe3f3 55%,#2f6ea8 100%);flex:none;position:relative;overflow:hidden}
.ribbon{position:absolute;left:-22px;top:12px;width:80px;height:13px;background:var(--blue);transform:rotate(-45deg)}
.result-body{flex:1}
.result-body h2{font-size:14px;color:var(--blue);font-weight:700;line-height:1.1}
.line{font-size:9.5px;color:var(--blue);margin-top:2px}
.ports{font-size:9px;color:var(--ink);margin-top:1px}
.dates{font-size:8.5px;color:var(--muted);margin-top:1px}
.dates b{color:var(--ink);font-weight:600}
.prices{display:flex;margin-top:8px;border:1px solid var(--line)}
.prices div{flex:1;text-align:center;border-right:1px solid var(--line);padding:3px 0;font-size:7px;color:var(--muted);line-height:1.3}
.prices div:last-child{border-right:none}
.prices strong{display:block;font-size:9.5px;color:var(--blue)}
.select{position:absolute;right:8px;bottom:8px;background:var(--nav);color:var(--white);font-size:8px;padding:3px 10px;border-radius:2px}
.select.on{background:var(--blue)}
.pager{display:flex;justify-content:flex-end;gap:3px;margin-top:14px}
.pager span{font-size:8px;border:1px solid var(--line);padding:2px 5px;color:var(--muted)}
.pager .current{background:var(--blue);color:var(--white);border-color:var(--blue)}

/* sidebar */
.sidebar{position:absolute;left:520px;top:158px;width:183px}
.panel{border:1px solid var(--line)}
.panel h3{background:var(--blue);color:var(--white);font-size:12.5px;font-weight:600;padding:6px 10px}
.panel-body{padding:8px 10px}
.field{height:18px;border:1px solid #ccc;margin-bottom:6px;font-size:8.5px;line-height:16px;padding:0 6px;color:var(--ink);position:relative}
.field::after{content:"";position:absolute;right:6px;top:6px;border:3px solid transparent;border-top-color:#777}
.note{font-size:8px;color:var(--blue)}
.search-row{display:flex;justify-content:space-between;align-items:center;margin-top:8px}
.search-row a{font-size:8px;color:var(--blue);text-decoration:none}
.btn{background:var(--blue);color:var(--white);font-size:8.5px;padding:3px 10px;border-radius:2px}
.newsletter{margin-top:20px;border:1px solid var(--line)}
.newsletter h3{font-size:11px;color:var(--ink);font-weight:600;padding:7px 10px;border-bottom:2px solid var(--blue)}
.newsletter-photo{height:84px;margin:8px 10px 0;background:linear-gradient(135deg,#f4c7a1 0%,#9fcbea 60%,#3b8dd0 100%)}
.newsletter p{font-size:9px;color:var(--ink);padding:6px 10px 0;line-height:1.3}
.newsletter .field::after{display:none}
.newsletter .field{margin:6px 10px 0;color:#aaa}
.newsletter .btn{display:inline-block;margin:6px 10px 10px}

/* partners */
.partners{position:absolute;left:93px;top:752px;width:610px}
.partners h2{font-size:15px;color:var(--blue);font-weight:600}
.partner-row{display:flex;justify-content:space-between;margin-top:14px}
.partner{width:108px;height:40px;border:1px solid var(--line);display:flex;align-items:center;justify-content:center}
.partner span{width:62px;height:14px;border-radius:2px;background:#c4ccd6}

/* footer */
.site-footer{position:absolute;top:925px;left:0;width:793px;height:275px;background:var(--footer);color:#bbb}
.footer-cols{position:absolute;left:93px;top:20px;width:610px;display:flex;gap:20px}
.footer-col{flex:1}
.footer-col h4{font-size:11px;color:var(--white);font-weight:600;margin-bottom:8px}
.footer-col ul{list-style:none}
.footer-col li{font-size:8px;line-height:1.9}
.footer-col li::before{content:"› ";color:var(--blue)}
.badge{width:44px;height:56px;background:#5b8ec2;border-radius:4px;float:left;margin-right:8px}
.footer-col p{font-size:8px;line-height:1.6}
.contact li::before{content:none}
.contact li{display:flex;align-items:center;gap:5px}
.contact svg{flex:none}
.footer-bottom{position:absolute;left:0;bottom:0;width:793px;height:42px;background:var(--footer-deep)}
.footer-bottom p{position:absolute;left:93px;top:10px;font-size:7.5px;line-height:1.5;color:#999}
.footer-icons{position:absolute;right:90px;top:14px;display:flex;gap:5px}
.footer-icons span{width:13px;height:13px;border-radius:50%;background:#666}
</style>
</head>
<body>

<header class="site-header">
  <div class="brand"><span class="brand-mark"></span><span class="brand-name">Haiyue Cruise</span></div>
  <div class="brand-url">www.haiyuecruise.example</div>
  <div class="header-tools">
    <div class="socials"><span></span><span></span><span></span><span></span><span class="lang">中文</span></div>
    <div class="call">
      <svg width="16" height="16" viewBox="0 0 16 16"><path d="M4 2l2.5 3-1.5 1.5a8 8 0 0 0 4.5 4.5L11 9.5 14 12l-1.5 2C7 14 2 9 2 3.5z" fill="var(--blue)"/></svg>
      <div><div class="call-label">Call Us Today</div><div class="call-number">4000 512 388</div></div>
    </div>
    <div class="account"><a href="#">Login</a><a href="#">Sign up</a></div>
  </div>
</header>

<nav class="main-nav">
  <ul>
    <li class="active">Home</li><li>Destination</li><li>Cruise Lines</li><li>Shore Excursion</li><li>Cruise Info</li><li>Deals</li><li>Online Booking</li><li>Contact Us</li><li>Blog</li><li>中文</li>
  </ul>
</nav>
<div class="breadcrumb"><p>Home &nbsp;›&nbsp; Search &nbsp;›&nbsp; Results</p></div>

<main class="results">
  <div class="results-head"><h1>Cruise Results</h1><small>76 Found</small></div>

  <article class="result">
    <div class="result-photo" role="img" aria-label="Cruise ship sailing on the open sea"></div>
    <div class="result-body">
      <h2>3 Days Bahamas</h2>
      <div class="line">Northwind Cruise Line : Northwind Star</div>
      <div class="ports">Miami, Great Stirrup Cay, Nassau, Miami</div>
      <div class="dates"><b>8 departure dates</b> : Sep 6, 13, 20, 27 2013</div>
      <div class="prices">
        <div>Inside from<strong>$174</strong>$58 per day</div>
        <div>Oceanview<strong>$174</strong>$58 per day</div>
        <div>Balcony<strong>$229</strong>$76 per day</div>
        <div>Suite<strong>$339</strong>$113 per day</div>
      </div>
    </div>
    <span class="select">Select</span>
  </article>

  <article class="result">
    <div class="result-photo" role="img" aria-label="Cruise ship sailing on the open sea"><span class="ribbon"></span></div>
    <div class="result-body">
      <h2>3 Days Bahamas</h2>
      <div class="line">Northwind Cruise Line : Northwind Star</div>
      <div class="ports">Miami, Great Stirrup Cay, Nassau, Miami</div>
      <div class="dates"><b>8 departure dates</b> : Sep 6, 13, 20, 27 2013</div>
      <div class="prices">
        <div>Inside from<strong>$174</strong>$58 per day</div>
        <div>Oceanview<strong>$174</strong>$58 per day</div>
        <div>Balcony<strong>$229</strong>$76 per day</div>
        <div>Suite<strong>$339</strong>$113 per day</div>
      </div>
    </div>
    <span class="select on">Select</span>
  </article>

  <article class="result">
    <div class="result-photo" role="img" aria-label="Cruise ship sailing on the open sea"><span class="ribbon"></span></div>
    <div class="result-body">
      <h2>3 Days Bahamas</h2>
      <div class="line">Northwind Cruise Line : Northwind Star</div>
      <div class="ports">Miami, Great Stirrup Cay, Nassau, Miami</div>
      <div class="dates"><b>8 departure dates</b> : Sep 6, 13, 20, 27 2013</div>
      <div class="prices">
        <div>Inside from<strong>$174</strong>$58 per day</div>
        <div>Oceanview<strong>$174</strong>$58 per day</div>
        <div>Balcony<strong>$229</strong>$76 per day</div>
        <div>Suite<strong>$339</strong>$113 per day</div>
      </div>
    </div>
    <span class="select">Select</span>
  </article>

  <div class="pager"><span>First</span><span>‹</span><span class="current">1</span><span>2</span><span>3</span><span>4</span><span>5</span><span>›</span><span>Last</span></div>
</main>

<aside class="sidebar">
  <section class="panel">
    <h3>Search Cruises</h3>
    <div class="panel-body">
      <div class="field">Asia</div>
      <div class="field">July 2013</div>
      <div class="field">Any Length</div>
      <div class="field">Any Cruise Line</div>
      <div class="note">More than 10,000 cruises to go</div>
      <div class="search-row"><a href="#">Advance Search</a><span class="btn">Search</span></div>
    </div>
  </section>
  <section class="newsletter">
    <h3>Cruise Deals Newsletter</h3>
    <div class="newsletter-photo" role="img" aria-label="Happy travellers relaxing on a sunny cruise deck"></div>
    <p>Subscribe to the best cruise deals now!</p>
    <div class="field">Your email here</div>
    <span class="btn">Subscribe</span>
  </section>
</aside>

<section class="partners">
  <h2>Our Reliable Partners</h2>
  <div class="partner-row">
    <div class="partner"><span></span></div>
    <div class="partner"><span></span></div>
    <div class="partner"><span></span></div>
    <div class="partner"><span></span></div>
    <div class="partner"><span></span></div>
  </div>
</section>

<footer class="site-footer">
  <div class="footer-cols">
    <div class="footer-col">
      <h4>Useful Pages</h4>
      <ul><li>Home</li><li>About us</li><li>Contact us</li><li>FAQ</li><li>Terms of Use</li><li>Payment</li><li>Booking Policy</li></ul>
    </div>
    <div class="footer-col">
      <h4>Cruise Info</h4>
      <ul><li>Cruise Lines</li><li>Ports</li><li>Shore Excursions</li><li>Destinations</li></ul>
    </div>
    <div class="footer-col">
      <h4>About haiyuecruise.example</h4>
      <span class="badge"></span>
      <p>We help Chinese travellers find and book the right cruise with clear prices and friendly support.</p>
    </div>
    <div class="footer-col">
      <h4>Contact us</h4>
      <ul class="contact">
        <li><svg width="9" height="9" viewBox="0 0 10 10"><path d="M5 0a3.5 3.5 0 0 0-3.5 3.5C1.5 6 5 10 5 10s3.5-4 3.5-6.5A3.5 3.5 0 0 0 5 0z" fill="var(--blue)"/></svg>Room 1201, 88 Harbor Road, Shanghai</li>
        <li><svg width="9" height="9" viewBox="0 0 10 10"><path d="M2 1l2 2-1 1a5 5 0 0 0 3 3l1-1 2 2-1 1C4 9 1 6 1 2z" fill="var(--blue)"/></svg>4000 512 388</li>
        <li><svg width="9" height="9" viewBox="0 0 10 10"><rect x="0.5" y="2" width="9" height="6" fill="none" stroke="var(--blue)"/><path d="M.5 2L5 5.5 9.5 2" fill="none" stroke="var(--blue)"/></svg>info@haiyuecruise.example</li>
      </ul>
    </div>
  </div>
  <div class="footer-bottom">
    <p>Copyright © 2013 Haiyue Cruise. All rights reserved.<br>沪ICP备00000000号</p>
    <div class="footer-icons"><span></span><span></span><span></span><span></span></div>
  </div>
</footer>

</body>
</html>
```